Dietary supplement, Clean and simple.

Hi,
I’d like to talk about the project,

About us:
We are a dietary supplement (Vitamins, Minerals, amino acids etc.) company.
The goal is to have about 25 products at the end of this year. However, for this goal to be achieved we need a good label design to make our products represent our company values.
I’ll be here every day supporting your questions, we are fully committed to making the highest/best quality/customer experience possible.

About the design and our values:
- Professional (We are in the industry of professionalism and expertise. I would love to show we are competent at this, Id. Like to have the labels looks like we have done our research.)
- Efficient (White spacing, good use of the space available.)
- Simple (Straight forward, in 5 seconds they have to know what the product they have is/how functions. We’re trying to simplify it for the consumer.
- No distractions (the only visually “distracting” factor can be the vector art.)

The guidelines:
The goal is to have a universal design, with one element that changes (Vector art). I’ll attach a file/multiple files I think can show some visuals on what I’m looking for, and what parts of the design I think are good/bad.

Label size: 69x155mm (Front is 77.5mm)

Design whatever you think fits our image. You’re the design expert, all I care about is that it fits our company standards/image.

Use this color/font.
Font: Sans Serif
Main company color is Mind green #237D62 (Use this color for something in the design.)

What I thought would be cool/might looks ugly, who knows:
1. The front of the label: Should have 1 vector art, preferably in the top right corner. (That looks good in multiple colors. The vector can have multiple areas to color, I would prefer 2 main colors in the vector art. The interchangeable colors are used for multiple kinds of products.)
2. Text/product information on the left. The text that will have to be displayed:
- Product name for instance “Magnesium + B6”
- Description for the product for instance “Magnesium with ginger taste”
- Company name or logo. (Add ® behind it. We are soon to be trademark registered.)
3. We need to show the "daily intake" amount on the front and also the amount in the complete bottle. For instance, “Daily intake 1 capsule, 60 capsules”.
• You don’t have to design the backside of the label. After I chose a design, I’d like to chat and give specific information on what areas need to be assigned where. (Too complex because of the law.)
Updates

Hi, Please make the deadline 31 days total. I want designers to have the time to design. And not be rushed to finish it.

I want to extend the deadline because i feel like a slightly more medical look would be interesting. Hope you can come up with something!!

Target Market(s)

Dietary supplement consumers

Industry/Entity Type

Dietary supplements

Font styles to use
Sans Serif

Colors

Designer to choose colors to be used in the design.

Requirements
Must have
• Trademark icon "®" has to be at the top right after the company logo(text of logo)/name.

```html
<!DOCTYPE html>
<html lang="en">
<head>
<meta charset="UTF-8">
<title>Calmwood Magnesium + B6 Label</title>
<link href="https://fonts.googleapis.com/css2?family=Open+Sans:ital,wght@0,400;0,600;0,700;1,600&display=swap" rel="stylesheet">
<style>
  :root {
    --mind-green: #237D62;
    --leaf-pale: #e6f4c8;
    --leaf-light: #b9de6e;
    --leaf-mid: #86c24a;
    --leaf-deep: #3f8f3a;
    --ink: #161616;
    --ginger: #f3a947;
    --ginger-edge: #b8843c;
    --count-teal: #8cbcaa;
    --white: #ffffff;
    --page: #ffffff;
  }
  * { margin: 0; padding: 0; box-sizing: border-box; }
  html, body {
    width: 1200px; height: 1200px; overflow: hidden;
    background: var(--page);
    font-family: "Open Sans", Arial, sans-serif;
  }
  .label {
    position: absolute; left: 85px; top: 391px;
    width: 1030px; height: 418px; overflow: hidden;
    background: var(--white);
  }
  .label-backdrop {
    position: absolute; inset: 0;
    background: linear-gradient(180deg,
      var(--white) 0%, var(--white) 38%,
      var(--leaf-pale) 47%, var(--leaf-light) 62%,
      var(--leaf-mid) 80%, var(--leaf-deep) 100%);
  }
  .brand {
    position: absolute; left: 0; right: 0; top: 70px;
    text-align: center;
    font-size: 54px; font-weight: 700; line-height: 1;
    color: var(--mind-green);
  }
  .brand sup {
    font-size: 16px; font-weight: 400; vertical-align: top;
    position: relative; top: -2px; margin-left: 2px;
  }
  .product-name {
    position: absolute; left: 291px; top: 175px;
    font-size: 40px; font-weight: 600; line-height: 1;
    color: var(--ink);
  }
  .product-tagline {
    position: absolute; left: 291px; top: 227px;
    width: 291px; height: 29px;
    background: var(--ginger);
    border-radius: 10px;
    box-shadow: 2px 2px 0 var(--ginger-edge);
    font-size: 17px; font-weight: 700; color: #2a2a2a;
    line-height: 29px; padding-left: 10px; letter-spacing: 0.2px;
  }
  .category {
    position: absolute; left: 289px; top: 368px;
    font-size: 19px; font-weight: 600; line-height: 1;
    color: var(--white); letter-spacing: 0.4px;
  }
  .dosage {
    position: absolute; left: 565px; top: 361px;
    width: 175px; height: 35px;
    background: var(--white); border-radius: 18px;
    display: flex; align-items: center;
  }
  .dosage-count {
    width: 72px; height: 35px; border-radius: 18px;
    background: var(--count-teal);
    display: flex; flex-direction: column; align-items: center; justify-content: center;
    color: #1e3a33; line-height: 1;
  }
  .dosage-count .number { font-size: 21px; font-weight: 600; }
  .dosage-count .unit { font-size: 6px; font-weight: 600; margin-top: 1px; }
  .dosage-intake {
    flex: 1; text-align: center; line-height: 1.1;
    font-style: italic; font-weight: 600; color: var(--ink);
  }
  .dosage-intake .caption { font-size: 11px; display: block; }
  .dosage-intake .amount { font-size: 13px; display: block; }
</style>
</head>
<body>
  <section class="label">
    <div class="label-backdrop" role="img" aria-label="Soft flowing green wave backdrop rising from the lower left to the upper right"></div>
    <div class="brand">Calmwood<sup>®</sup></div>
    <h1 class="product-name">MAGNESIUM + B6</h1>
    <p class="product-tagline">Magnesium with ginger taste</p>
    <p class="category">DIETARY SUPPLEMENT</p>
    <div class="dosage">
      <div class="dosage-count"><span class="number">60</span><span class="unit">CAPSULES</span></div>
      <div class="dosage-intake"><span class="caption">Daily Intake</span><span class="amount">1 CAPSULE</span></div>
    </div>
  </section>
</body>
</html>
```